MBR - Stationery Design Project

We need stationery based on our logo.

Company info :
Cabinet Voisard & Associés
Société à responsabilité limitée au capital de 200.000 FCFP
RCS Papeete 27586K - Numéro tahiti K73962
Centre d’affaires OPALE - Rue Gaston Perrin
BP 61384 MAHU POTE - 98752 Papeete
Tahiti - Polynésie française
Tél : +689 40 73 16 48
Fax : +689 40 39 64 91

Industry/Entity Type

It Company

Font styles to use
Sans Serif

```html
<!DOCTYPE html>
<html lang="fr">
<head>
<meta charset="utf-8">
<title>MBR – Compliment Slip</title>
<link rel="stylesheet" href="https://fonts.googleapis.com/css2?family=Josefin+Sans:wght@300;400&display=swap">
<style>
  :root {
    --backdrop: #dcdcdc;
    --paper: #f4f4f4;
    --navy: #15294b;
    --slate: #7a8c8d;
    --ink: #2a2a2a;
    --rule: #9a9a9a;
  }
  * { box-sizing: border-box; margin: 0; padding: 0; }
  html, body {
    width: 1200px; height: 1000px; overflow: hidden;
    background: var(--backdrop);
    font-family: "Josefin Sans", "Helvetica Neue", Arial, sans-serif;
  }
  .slip {
    position: absolute; left: 100px; top: 265px;
    width: 1000px; height: 470px;
    background: var(--paper);
    overflow: hidden;
  }
  .slip__band {
    position: absolute; left: 430px; top: 0;
    width: 570px; height: 110px;
    background: var(--slate);
  }
  .slip__block {
    position: absolute; left: 0; top: 110px;
    width: 140px; height: 115px;
    background: var(--navy);
  }
  .brand {
    position: absolute; left: 152px; top: 96px;
    color: var(--navy);
  }
  .brand__name {
    font-weight: 300; font-size: 104px; line-height: 1;
    letter-spacing: -2px;
  }
  .brand__company {
    font-weight: 300; font-size: 22px; margin-top: -4px;
  }
  .brand__tagline {
    font-weight: 300; font-size: 11px; margin-top: 4px; letter-spacing: 0.5px;
  }
  .slip__title {
    position: absolute; left: 560px; top: 186px;
    font-weight: 300; font-size: 32px; letter-spacing: 1px;
    color: var(--ink);
  }
  .slip__divider {
    position: absolute; left: 152px; top: 262px;
    width: 640px; height: 1px; background: var(--rule);
  }
  .legal {
    position: absolute; left: 0; right: 0; top: 405px;
    border-top: 1px solid var(--rule);
    padding: 8px 40px 0;
    font-weight: 300; font-size: 10px; line-height: 1.5;
    color: var(--ink);
  }
</style>
</head>
<body>
  <main class="slip">
    <div class="slip__band"></div>
    <div class="slip__block"></div>
    <div class="brand">
      <div class="brand__name">MBR</div>
      <div class="brand__company">Cabinet Voisard &amp; Associés</div>
      <div class="brand__tagline">Expertise-comptable • Audit • Conseil</div>
    </div>
    <h1 class="slip__title">WITH COMPLIMENT.</h1>
    <div class="slip__divider"></div>
    <footer class="legal">
      <p>Cabinet Voisard &amp; Associés - Société à responsabilité limitée au capital de 200.000 FCFP - RCS Papeete 27586K - Numéro tahiti K73962</p>
      <p>Centre d’affaires OPALE - Rue Gaston Perrin BP 61384 MAHU POTE - 98752 Papeete Tahiti - Polynésie française - Tél : +689 40 73 16 48 | Fax : +689 40 39 64 91</p>
    </footer>
  </main>
</body>
</html>
```